TALMORK

The business want a professional looking business card. We have a scetch we will add but want the extra upgrade, and would like more suggestions for variations of our business cards.

```html
<!DOCTYPE html>
<html lang="en">
<head>
<meta charset="utf-8">
<title>TALMORK Business Card</title>
<link rel="stylesheet" href="https://fonts.googleapis.com/css2?family=Montserrat:wght@300;400;500;700&display=swap">
<style>
  :root {
    --page-bg: #1b1b1b;
    --card-bg: #1f1f1f;
    --card-back-bg: #1c1c1c;
    --gold: #c9a24a;
    --text-light: #f2f2f2;
    --pattern-dark: #141414;
    --pattern-light: #5a5a5a;
  }
  * { margin: 0; padding: 0; box-sizing: border-box; }
  html, body { width: 1200px; height: 1059px; overflow: hidden; }
  body {
    background: var(--page-bg);
    font-family: "Montserrat", sans-serif;
    position: relative;
  }
  .card {
    position: absolute;
    width: 690px;
    height: 392px;
    border-radius: 18px;
    overflow: hidden;
  }
  .card-front { left: 256px; top: 89px; background: var(--card-bg); }
  .card-back { left: 255px; top: 547px; background: var(--card-back-bg); }

  .brand {
    position: absolute;
    text-align: center;
    color: var(--gold);
  }
  .brand-dot {
    display: block;
    margin: 0 auto;
    border-radius: 50%;
    background: var(--gold);
  }
  .brand-name {
    display: block;
    font-weight: 500;
    letter-spacing: 0.22em;
    line-height: 1;
  }
  .brand-tagline {
    display: block;
    font-weight: 500;
    letter-spacing: 0.42em;
    line-height: 1;
  }
  .card-front .brand { left: 75px; top: 122px; width: 210px; }
  .card-front .brand-dot { width: 58px; height: 58px; margin-bottom: 56px; }
  .card-front .brand-name { font-size: 27px; margin-right: -0.22em; }
  .card-front .brand-tagline { font-size: 9px; margin-top: 10px; margin-right: -0.42em; }

  .contact-block { position: absolute; left: 347px; top: 103px; }
  .person-name {
    color: var(--gold);
    font-weight: 700;
    font-size: 23.5px;
    line-height: 1.1;
  }
  .person-role {
    color: var(--text-light);
    font-weight: 400;
    font-size: 18px;
    margin-top: 3px;
  }
  .divider {
    width: 14px;
    height: 1px;
    background: var(--gold);
    margin: 24px 0 20px;
  }
  .contact-list { list-style: none; }
  .contact-item {
    display: flex;
    align-items: center;
    color: var(--text-light);
    font-size: 18.5px;
    font-weight: 400;
    height: 32px;
  }
  .contact-icon { width: 14px; height: 14px; margin: 0 10px 0 2px; flex: none; }

  .back-pattern {
    position: absolute;
    inset: 0;
    background: linear-gradient(100deg, var(--pattern-dark) 0%, #262626 45%, var(--pattern-light) 100%);
    opacity: 0.55;
  }
  .back-panel {
    position: absolute;
    left: 462px;
    top: 160px;
    width: 165px;
    height: 150px;
    background: var(--card-back-bg);
  }
  .card-back .brand { left: 462px; top: 170px; width: 165px; }
  .card-back .brand-dot { width: 44px; height: 44px; margin-bottom: 34px; }
  .card-back .brand-name { font-size: 20px; margin-right: -0.22em; }
  .card-back .brand-tagline { font-size: 7px; margin-top: 8px; margin-right: -0.42em; }
</style>
</head>
<body>
  <section class="card card-front">
    <div class="brand">
      <span class="brand-dot"></span>
      <span class="brand-name">TALMORK</span>
      <span class="brand-tagline">SINCE 2026</span>
    </div>
    <div class="contact-block">
      <p class="person-name">Henrik Aasmund Solberg</p>
      <p class="person-role">CEO &amp; Founder</p>
      <div class="divider"></div>
      <ul class="contact-list">
        <li class="contact-item">
          <svg class="contact-icon" viewBox="0 0 24 24"><path fill="#c9a24a" d="M6.6 10.8a15 15 0 0 0 6.6 6.6l2.2-2.2a1 1 0 0 1 1-.25 11.4 11.4 0 0 0 3.6.57 1 1 0 0 1 1 1V20a1 1 0 0 1-1 1A17 17 0 0 1 3 4a1 1 0 0 1 1-1h3.5a1 1 0 0 1 1 1c0 1.25.2 2.45.57 3.57a1 1 0 0 1-.25 1z"/></svg>
          004791835274
        </li>
        <li class="contact-item">
          <svg class="contact-icon" viewBox="0 0 24 24"><path fill="#c9a24a" d="M2 9l10-7 10 7v12H2z"/><path fill="#1f1f1f" d="M4 10l8 6 8-6v1l-8 6-8-6z"/></svg>
          talmork.llc@mailbox.com
        </li>
        <li class="contact-item">
          <svg class="contact-icon" viewBox="0 0 24 24"><circle cx="12" cy="12" r="10" fill="#c9a24a"/><path fill="#1f1f1f" d="M7 6c2 1 3 3 2 5s1 3 2 5-1 3-2 3c-2-2-4-5-4-8 0-2 1-4 2-5zm8-1c2 1 4 3 4 6-1 0-3 0-3 2s-1 3-2 3c0-2-2-3-1-5s2-2 2-3-1-2 0-3z"/></svg>
          www.talmork.llc
        </li>
      </ul>
    </div>
  </section>

  <section class="card card-back">
    <div class="back-pattern" role="img" aria-label="Repeating tonal pattern of brand emblems fading from black to grey"></div>
    <div class="back-panel"></div>
    <div class="brand">
      <span class="brand-dot"></span>
      <span class="brand-name">TALMORK</span>
      <span class="brand-tagline">SINCE 2026</span>
    </div>
  </section>
</body>
</html>
```